Medspa business needs a webpage

we need a website for a new Medspa company based in Cedar Bend, OR called Velora Glow Medical Aesthetics. We offer non surgical, cosmetic procedures as well as medical weight loss. We would like a sleek design, with rich colors (dark, emerald green and gold). The website should list our services, pricing and links to book appointments.

```html
<!DOCTYPE html>
<html lang="en">
<head>
<meta charset="utf-8">
<title>Velora Glow Medical Aesthetics</title>
<link href="https://fonts.googleapis.com/css2?family=Montserrat:wght@300;400;500;600&family=Cinzel:wght@400;500&display=swap" rel="stylesheet">
<style>
:root{
  --forest:#0f2a12;
  --gold:#b79c45;
  --gold-soft:#d8c68e;
  --ink:#2c2c2c;
  --muted:#777;
  --line:#e4dccb;
  --white:#ffffff;
}
*{box-sizing:border-box;margin:0;padding:0}
html,body{width:1200px;height:2544px;overflow:hidden}
body{font-family:"Montserrat",sans-serif;color:var(--ink);background:var(--white)}
.page{position:relative;width:1200px;height:2544px;overflow:hidden;background:var(--white)}
.abs{position:absolute}
.btn{display:inline-block;font-size:11px;font-weight:500;padding:9px 18px;background:var(--gold);color:var(--white);letter-spacing:.5px;white-space:nowrap}
.btn-dark{background:var(--forest);color:var(--white)}
.display{font-family:"Cinzel",serif;font-weight:400;color:var(--gold);letter-spacing:2px;white-space:nowrap}
.photo{border-radius:4px}

/* header */
.site-header{left:0;top:0;width:1200px;height:38px;background:var(--forest);z-index:5}
.brand{left:262px;top:6px;display:flex;align-items:center;gap:8px;color:var(--gold-soft);font-family:"Cinzel",serif;font-size:15px;letter-spacing:2px;line-height:16px}
.brand-dot{width:18px;height:18px;border-radius:50%;background:var(--gold)}
.brand small{display:block;font-size:8px;letter-spacing:3px;line-height:10px}
.nav{right:128px;top:12px;display:flex;gap:22px;font-size:10px;color:var(--white)}
.nav .active{color:var(--gold-soft)}
.nav-cta{right:24px;top:8px;font-size:10px;color:var(--white);border:1px solid var(--gold);padding:4px 10px}

/* hero */
.hero-glow{left:560px;top:40px;width:640px;height:540px;background:radial-gradient(circle at 55% 45%,#f3ead2 0%,#faf6ec 45%,rgba(255,255,255,0) 70%)}
.hero-kicker{left:262px;top:158px;font-size:15px;letter-spacing:2px;color:var(--gold)}
.hero-title{left:258px;top:180px;font-size:60px;line-height:58px}
.hero-sub{left:262px;top:300px;font-size:16px;letter-spacing:2px;color:var(--gold)}
.hero-text{left:262px;top:340px;width:250px;font-size:10px;line-height:15px;color:var(--muted)}
.hero-actions{left:262px;top:420px;display:flex;gap:10px}
.hero-photo{left:730px;top:50px;width:340px;height:460px;border-radius:170px 170px 0 0;background:linear-gradient(160deg,#e8d6c2,#c9a98d 60%,#ece2d2)}
.hero-ring{left:670px;top:80px;width:90px;height:90px;border-radius:50%;border:1px solid var(--gold);background:var(--white)}

/* welcome */
.team-photo{top:560px;width:136px;height:180px;background:linear-gradient(170deg,#3a2b24,#8c6a56 55%,#d9c6b4)}
.team-name{top:752px;width:136px;text-align:center;font-size:10px;color:var(--ink)}
.welcome-kicker{left:628px;top:578px;font-size:13px;letter-spacing:2px;color:var(--gold)}
.welcome-title{left:626px;top:596px;font-size:40px;line-height:40px}
.welcome-sub{left:628px;top:640px;font-size:18px;letter-spacing:2px;color:var(--gold)}
.welcome-text{left:628px;top:676px;width:300px;font-size:9px;line-height:14px;color:var(--muted)}
.welcome-btn{left:628px;top:748px}
.divider-dot{left:596px;top:514px;width:8px;height:8px;border-radius:50%;border:1px solid var(--gold)}

/* services */
.section-title{width:1200px;left:0;text-align:center;font-size:40px}
.services-title{top:860px}
.service-card{top:944px;width:300px;height:200px;border:1px solid var(--line);background:var(--white)}
.service-card h3{position:absolute;left:14px;top:14px;font-size:12px;font-weight:500;color:var(--ink)}
.service-card p{position:absolute;left:14px;top:36px;width:130px;font-size:8.5px;line-height:13px;color:var(--muted)}
.service-card ul{position:absolute;left:14px;top:110px;list-style:none;font-size:8.5px;line-height:14px;color:var(--muted)}
.service-card .btn{position:absolute;left:14px;bottom:14px;font-size:9px;padding:6px 12px}
.service-photo{position:absolute;right:10px;top:20px;width:140px;height:160px;border-radius:70px 70px 6px 6px}

/* pricing */
.pricing-band{left:0;top:1200px;width:1200px;height:460px;background:var(--forest)}
.pricing-title{top:1252px;color:var(--gold-soft)}
.price-card{top:1370px;width:222px;height:180px;background:var(--white);padding:16px}
.price-card h4{font-size:12px;font-weight:500;color:var(--ink)}
.price{margin-top:8px;font-family:"Cinzel",serif;font-size:24px;color:var(--gold);white-space:nowrap}
.price span{font-family:"Montserrat",sans-serif;font-size:9px;color:var(--muted)}
.price-card ul{margin-top:10px;list-style:none;font-size:8.5px;line-height:15px;color:var(--muted)}
.price-card ul li::before{content:"\2022 ";color:var(--gold)}
.price-card .btn{position:absolute;left:16px;bottom:16px;font-size:9px;padding:5px 12px}
.pricing-note{left:0;top:1590px;width:1200px;text-align:center;font-size:8.5px;color:#b8b8a6}

/* cta */
.cta-photo{left:100px;top:1650px;width:720px;height:330px;background:linear-gradient(100deg,#d9cfc4,#c6a893 40%,#e8dfd6 75%,#f3efea)}
.cta-box{left:650px;top:1720px;width:430px;height:250px;background:var(--gold);padding:60px 40px;text-align:center}
.cta-box h2{font-family:"Cinzel",serif;font-weight:400;font-size:40px;line-height:44px;color:var(--forest);white-space:nowrap}
.cta-box p{margin-top:8px;font-size:14px;line-height:20px;color:var(--forest)}
.cta-actions{margin-top:16px;display:flex;justify-content:center;gap:8px}
.cta-actions .btn{font-size:10px;padding:7px 12px}

/* contact */
.contact-form{left:262px;top:2060px;width:290px}
.field{margin-bottom:10px}
.field label{display:block;font-size:9px;color:var(--ink);margin-bottom:3px}
.field div{height:22px;border:1px solid var(--line);font-size:8.5px;color:#aaa;padding:5px 8px}
.field .tall{height:56px}
.contact-form .btn{width:100%;text-align:center;font-size:9px;padding:7px 0}
.form-note{margin-top:8px;font-size:8px;color:var(--muted)}
.visit-title{left:600px;top:2060px;font-size:40px;line-height:44px;letter-spacing:1px}
.visit-sub{left:602px;top:2106px;font-size:10px;color:var(--muted)}
.visit-dir{left:602px;top:2124px;font-size:16px;color:var(--gold)}
.visit-info{left:602px;top:2160px;font-size:9px;line-height:15px;color:var(--muted)}
.visit-info svg{vertical-align:middle;margin-right:4px}

/* footer */
.site-footer{left:0;top:2490px;width:1200px;height:54px;background:var(--forest);color:#c9c4b0;font-size:9px}
.site-footer .copy{position:absolute;left:262px;top:22px}
.site-footer .links{position:absolute;right:262px;top:22px;display:flex;gap:16px}
</style>
</head>
<body>
<div class="page">

  <section class="hero">
    <div class="hero-glow abs"></div>
    <div class="hero-kicker abs">ELEVATE YOUR</div>
    <h1 class="hero-title display abs">SKIN<br>ENHANCE</h1>
    <div class="hero-sub abs">YOUR CONFIDENCE.</div>
    <p class="hero-text abs">Non surgical aesthetic treatments and medical weight loss, tailored to you by experienced providers in Cedar Bend, OR.</p>
    <div class="hero-actions abs"><span class="btn">Book Appointment</span><span class="btn btn-dark">View Services</span></div>
    <div class="hero-photo abs" role="img" aria-label="Portrait of a woman with glowing skin"></div>
    <div class="hero-ring abs"></div>
  </section>

  <header class="site-header abs">
    <div class="brand abs"><span class="brand-dot"></span><div>VELORA GLOW<small>MEDICAL AESTHETICS</small></div></div>
    <nav class="nav abs"><span class="active">Home</span><span>Services</span><span>Pricing</span><span>Team</span><span>Contact</span></nav>
    <span class="nav-cta abs">Book Now</span>
  </header>

  <div class="divider-dot abs"></div>

  <section class="welcome">
    <div class="team-photo photo abs" style="left:264px" role="img" aria-label="Provider portrait"></div>
    <div class="team-name abs" style="left:264px">Maren Holt | ARNP</div>
    <div class="team-photo photo abs" style="left:416px" role="img" aria-label="Provider portrait"></div>
    <div class="team-name abs" style="left:416px">Dana Ruiz | PA-C</div>
    <div class="welcome-kicker abs">WELCOME TO</div>
    <h2 class="welcome-title display abs">VELORA GLOW</h2>
    <div class="welcome-sub abs">MEDICAL AESTHETICS</div>
    <p class="welcome-text abs">Velora Glow Medical Aesthetics offers advanced, non surgical treatments in a calm and welcoming space. Our licensed providers build every plan around your goals, so you leave looking refreshed, natural and confident in your own skin.</p>
    <span class="welcome-btn btn abs">Meet Our Team</span>
  </section>

  <section class="services">
    <h2 class="section-title services-title display abs">OUR SERVICES</h2>
    <article class="service-card abs" style="left:120px">
      <h3>INJECTABLES</h3>
      <p>Smooth lines and restore volume with precise, natural looking results.</p>
      <ul><li>Neurotoxins</li><li>Dermal fillers</li><li>Lip enhancement</li></ul>
      <span class="btn">Learn More</span>
      <div class="service-photo" style="background:linear-gradient(160deg,#e9dccd,#c8a58c)" role="img" aria-label="Injectable treatment"></div>
    </article>
    <article class="service-card abs" style="left:450px">
      <h3>Skin Rejuvenation</h3>
      <p>Renew texture and tone with treatments that boost collagen.</p>
      <ul><li>Microneedling</li><li>Chemical peels</li><li>Facials</li></ul>
      <span class="btn">Learn More</span>
      <div class="service-photo" style="background:linear-gradient(160deg,#eee4d8,#b89a86)" role="img" aria-label="Skin rejuvenation result"></div>
    </article>
    <article class="service-card abs" style="left:780px">
      <h3>Medical Weight Loss</h3>
      <p>Provider guided programs to help you reach lasting goals.</p>
      <ul><li>GLP-1 therapy</li><li>Nutrition plans</li><li>Check-ins</li></ul>
      <span class="btn">Learn More</span>
      <div class="service-photo" style="background:linear-gradient(160deg,#f0e7dd,#cdb29c)" role="img" aria-label="Weight loss program"></div>
    </article>
  </section>

  <section class="pricing">
    <div class="pricing-band abs"></div>
    <h2 class="section-title pricing-title display abs">TRANSPARENT PRICING</h2>
    <article class="price-card abs" style="left:120px">
      <h4>Neuromodulators</h4>
      <div class="price">$12-$14 <span>/unit</span></div>
      <ul><li>Forehead lines</li><li>Crow's feet</li><li>Frown lines</li></ul>
      <span class="btn">Book</span>
    </article>
    <article class="price-card abs" style="left:366px">
      <h4>Dermal Fillers</h4>
      <div class="price">$650-$800 <span>/syringe</span></div>
      <ul><li>Lips and cheeks</li><li>Jawline</li><li>Under eyes</li></ul>
      <span class="btn">Book</span>
    </article>
    <article class="price-card abs" style="left:612px">
      <h4>Microneedling</h4>
      <div class="price">$295 <span>/session</span></div>
      <ul><li>Texture and tone</li><li>Acne scars</li><li>Fine lines</li></ul>
      <span class="btn">Book</span>
    </article>
    <article class="price-card abs" style="left:858px">
      <h4>Weight Loss Program</h4>
      <div class="price">$349 <span>/month</span></div>
      <ul><li>Medication</li><li>Monthly visits</li><li>Ongoing support</li></ul>
      <span class="btn">Book</span>
    </article>
    <p class="pricing-note abs">* Pricing may vary by treatment plan. Consultations are complimentary.</p>
  </section>

  <section class="cta">
    <div class="cta-photo abs" role="img" aria-label="Woman receiving a facial treatment from gloved hands"></div>
    <div class="cta-box abs">
      <h2>Ready to glow?</h2>
      <p>Reserve your appointment in minutes.<br>New patients welcome.</p>
      <div class="cta-actions"><span class="btn btn-dark">Book Online</span><span class="btn btn-dark">Call (360) 555-0142</span></div>
    </div>
  </section>

  <section class="contact">
    <div class="contact-form abs">
      <div class="field"><label>Name</label><div>Your name</div></div>
      <div class="field"><label>Email</label><div>Your email</div></div>
      <div class="field"><label>Service</label><div>Select</div></div>
      <div class="field"><label>Message</label><div class="tall">How can we help?</div></div>
      <span class="btn">Send Message</span>
      <p class="form-note">We reply within one business day.</p>
    </div>
    <h2 class="visit-title display abs">Visit Us</h2>
    <div class="visit-sub abs">Cedar Bend, OR</div>
    <div class="visit-dir abs">Get directions &rarr;</div>
    <div class="visit-info abs">
      <div><svg width="9" height="9" viewBox="0 0 10 10"><path d="M2 1l2 2-1 1.5c.8 1.3 1.7 2.2 3 3L7.5 6.5l2 2-1.5 1.5C4 9.5.5 6 0 2.5z" fill="#b79c45"/></svg>(360) 555-0142</div>
      <div><svg width="9" height="9" viewBox="0 0 10 10"><rect x="0.5" y="2" width="9" height="6" fill="none" stroke="#b79c45"/><path d="M.5 2l4.5 3.5L9.5 2" fill="none" stroke="#b79c45"/></svg>hello@veloraglow.com</div>
      <div><svg width="9" height="9" viewBox="0 0 10 10"><path d="M5 0a3.5 3.5 0 0 1 3.5 3.5C8.5 6 5 10 5 10S1.5 6 1.5 3.5A3.5 3.5 0 0 1 5 0z" fill="#b79c45"/></svg>Mon-Sat by appt</div>
    </div>
  </section>

  <footer class="site-footer abs">
    <span class="copy">&copy; 2025 Velora Glow Medical Aesthetics &middot; Cedar Bend, OR</span>
    <div class="links"><span>Services</span><span>Pricing</span><span>Book</span><span>Privacy</span></div>
  </footer>

</div>
</body>
</html>
```